Automotive eCommerce Business looking for a business card design

Looking for a clean and simple business card design. Our company name is "Brindle Auto" and we are a company specializing in the ecommerce sales of automotive parts, specifically for pick up trucks and large SUVs. Our company colours are red, black, and white.

Feel free to use the logo provided or create a new logo that you seem fit. Looking forward to your creative ideas!

Industry/Entity Type

Automotive

Contact Information for Business Card

We were thinking of a possibly two-sided design featuring just the logo and company name on one side, and personal information on the other side. Single sided designs will be considered as well.

Font styles to use
Serif
Sans Serif
Decorative

Colors
ec1f27
ffffff
000000

Requirements
Must have
• Space for employee's name, title, phone number and email address, along with the company address and website somewhere.

```html
<!DOCTYPE html>
<html lang="en">
<head>
<meta charset="utf-8">
<title>Brindle Auto Ltd. – Business Card</title>
<link rel="stylesheet" href="https://fonts.googleapis.com/css2?family=Cinzel:wght@500&family=Roboto:wght@400;700&display=swap">
<style>
  :root {
    --backdrop: #d9d6d2;
    --card-top: #f4f4f3;
    --card-bottom: #e2e3e3;
    --card-edge: #ffffff;
    --band-red: #8e2a30;
    --band-red-dark: #6f1c22;
    --band-cap: #3a3b3e;
    --ink: #2a2a2a;
    --ink-soft: #3c3c3c;
    --accent-red: #8b1c25;
    --white: #ffffff;
  }
  html, body {
    margin: 0;
    width: 1200px;
    height: 969px;
    overflow: hidden;
    background: var(--backdrop);
  }
  .card {
    position: absolute;
    left: 100px;
    top: 198px;
    width: 1000px;
    height: 572px;
    border-radius: 26px;
    overflow: hidden;
    background: linear-gradient(160deg, var(--card-top), var(--card-bottom));
    box-shadow: inset 0 0 0 2px var(--card-edge), 0 18px 40px rgba(0,0,0,0.18);
    font-family: "Roboto", Arial, sans-serif;
  }
  .brand-band {
    position: absolute;
    left: 0;
    top: 0;
    width: 198px;
    height: 100%;
    background: linear-gradient(180deg, var(--band-red) 0%, var(--band-red-dark) 100%);
  }
  .brand-band__cap {
    position: absolute;
    left: 0;
    top: 0;
    width: 100%;
    height: 50px;
    background: var(--band-cap);
  }
  .brand-band__square {
    position: absolute;
    left: 54px;
    top: 100px;
    width: 90px;
    height: 90px;
    background: var(--white);
  }
  .contact-icons {
    position: absolute;
    left: 0;
    top: 0;
    width: 198px;
    height: 100%;
  }
  .company-name {
    position: absolute;
    left: 233px;
    top: 134px;
    margin: 0;
    font-family: "Cinzel", "Times New Roman", serif;
    font-weight: 500;
    font-size: 44px;
    letter-spacing: 0.5px;
    color: var(--ink);
    white-space: nowrap;
  }
  .contact-text {
    position: absolute;
    left: 233px;
    margin: 0;
    font-size: 24px;
    line-height: 31px;
    color: var(--ink-soft);
  }
  .contact-text--address { top: 290px; }
  .contact-text--lines { top: 366px; }
  .person {
    position: absolute;
    right: 60px;
    top: 448px;
    text-align: right;
  }
  .person__name {
    margin: 0;
    font-weight: 700;
    font-size: 31px;
    line-height: 36px;
    color: var(--accent-red);
    letter-spacing: 0.3px;
  }
  .person__title {
    margin: 2px 0 0;
    font-weight: 700;
    font-size: 23px;
    color: var(--ink);
    letter-spacing: 0.3px;
  }
</style>
</head>
<body>
  <main class="card">
    <div class="brand-band">
      <div class="brand-band__cap"></div>
      <div class="brand-band__square"></div>
      <svg class="contact-icons" viewBox="0 0 198 572" fill="var(--white)" aria-hidden="true">
        <!-- pin -->
        <path d="M98 285c-7 0-12 5-12 12 0 9 12 20 12 20s12-11 12-20c0-7-5-12-12-12zm0 16a4 4 0 1 1 0-8 4 4 0 0 1 0 8z"/>
        <!-- phone -->
        <path d="M90 375c2-2 4-2 5 0l3 4c1 1 1 3-1 4l-2 1c1 3 4 6 7 7l1-2c1-2 3-2 4-1l4 3c2 1 2 3 0 5l-2 2c-6 2-20-12-19-19z"/>
        <!-- mobile -->
        <rect x="92" y="403" width="13" height="21" rx="2" fill="none" stroke="var(--white)" stroke-width="2.5"/>
        <!-- fax -->
        <rect x="88" y="438" width="21" height="12" rx="2"/>
        <rect x="92" y="432" width="13" height="6"/>
        <!-- mail -->
        <rect x="88" y="470" width="21" height="14" rx="1"/>
        <path d="M88 471l10.5 8 10.5-8" fill="none" stroke="var(--band-red-dark)" stroke-width="2"/>
        <!-- globe -->
        <circle cx="98.5" cy="508" r="10"/>
        <path d="M88.5 508h20M98.5 498c-5 6-5 14 0 20M98.5 498c5 6 5 14 0 20" fill="none" stroke="var(--band-red-dark)" stroke-width="1.6"/>
      </svg>
    </div>

    <h1 class="company-name">Brindle Auto Ltd.</h1>

    <p class="contact-text contact-text--address">2140 Alder Row<br>Kenai, Alaska 34580</p>
    <p class="contact-text contact-text--lines">
      555 301 4172<br>
      555 782 6039<br>
      555 914 2850<br>
      hello@brindleauto.com<br>
      www.brindleauto.com
    </p>

    <div class="person">
      <p class="person__name">DANA REYES</p>
      <p class="person__title">CEO/FOUNDER</p>
    </div>
  </main>
</body>
</html>
```